Business Card Design for Occupational Medicine Start Up Company

We need to design a professional business card. We are a healthcare company providing occupational medicine services to blue collar industries. We are professional, efficient and high quality service providers.

Target Market(s)

Blue Collar Industry: Shipbuilding, Ports, Trucking Companies; The Executives and Safety Officers for these companies

Industry/Entity Type

Healthcare

Contact Information for Business Card

Logo, Name, Title, Email, Phone

Other font styles liked:
• Please match our Brand Guide

Requirements
Must have
• Our Company Colors and Logo

```html
<!DOCTYPE html>
<html lang="en">
<head>
<meta charset="utf-8">
<title>Harborline Business Card</title>
<link rel="stylesheet" href="https://fonts.googleapis.com/css2?family=Montserrat:wght@700&family=Roboto:wght@400;700&display=swap">
<style>
  :root {
    --navy: #27367f;
    --sky: #2aa0dc;
    --amber: #f1a93d;
    --white: #ffffff;
    --ink: #222222;
    --stage: #ececec;
  }
  * { margin: 0; padding: 0; box-sizing: border-box; }
  html, body { width: 995px; height: 1200px; overflow: hidden; }
  body { background: var(--stage); position: relative; font-family: "Roboto", Arial, sans-serif; }

  .card { position: absolute; box-shadow: 0 8px 18px rgba(0,0,0,0.28); overflow: hidden; }

  .card-front { left: 124px; top: 142px; width: 746px; height: 426px; background: var(--navy); }
  .card-front .brand-mark {
    position: absolute; left: 50%; top: 188px; width: 96px; height: 96px;
    margin: -48px 0 0 -48px; border-radius: 50%; background: var(--amber);
  }
  .card-front .brand-name {
    position: absolute; left: 0; right: 0; top: 262px; text-align: center;
    font-family: "Montserrat", Arial, sans-serif; font-weight: 700;
    font-size: 50px; letter-spacing: 1px; color: var(--white);
  }

  .card-back { left: 126px; top: 635px; width: 742px; height: 423px; background: var(--white); }
  .accent-bar { position: absolute; left: 0; top: 42px; width: 24px; height: 45px; background: var(--navy); }
  .holder-name {
    position: absolute; left: 39px; top: 34px;
    font-weight: 700; font-size: 33px; color: var(--navy); letter-spacing: -0.3px;
  }
  .holder-title { position: absolute; left: 39px; top: 72px; font-size: 17px; color: var(--ink); }

  .card-back .brand-mark {
    position: absolute; left: 524px; top: 42px; width: 82px; height: 82px;
    border-radius: 50%; background: var(--amber);
  }
  .card-back .brand-name {
    position: absolute; left: 425px; width: 280px; top: 133px; text-align: center;
    font-family: "Montserrat", Arial, sans-serif; font-weight: 700;
    font-size: 31px; letter-spacing: 0.5px; color: var(--navy);
  }

  .contact-list { position: absolute; left: 39px; top: 320px; list-style: none; }
  .contact-list li {
    display: flex; align-items: center; gap: 3px;
    font-size: 17.5px; line-height: 24px; color: var(--ink);
  }
  .contact-list svg { width: 13px; height: 13px; fill: var(--navy); flex: none; }
</style>
</head>
<body>
  <section class="card card-front" aria-label="Card front">
    <div class="brand-mark"></div>
    <div class="brand-name">HARBORLINE</div>
  </section>

  <section class="card card-back" aria-label="Card back">
    <div class="accent-bar"></div>
    <h1 class="holder-name">DANIEL BROOKS</h1>
    <p class="holder-title">Director</p>

    <div class="brand-mark"></div>
    <div class="brand-name">HARBORLINE</div>

    <ul class="contact-list">
      <li>
        <svg viewBox="0 0 16 16" aria-hidden="true"><path d="M4 1l2.5 3-1.5 2c1 2 2.5 3.5 4.5 4.5l2-1.5 3 2.5-1.5 2.5C7 15 1 9 1.5 2.5z"/></svg>
        (555)214 0386
      </li>
      <li>
        <svg viewBox="0 0 16 16" aria-hidden="true"><path d="M1 3h14v10H1z M2 4l6 5 6-5" fill="none" stroke="#27367f" stroke-width="1.6"/></svg>
        hello@harborline.com
      </li>
      <li>
        <svg viewBox="0 0 16 16" aria-hidden="true"><g fill="none" stroke="#27367f" stroke-width="1.3"><circle cx="8" cy="8" r="6.5"/><ellipse cx="8" cy="8" rx="3" ry="6.5"/><path d="M1.5 8h13M3 4.5h10M3 11.5h10"/></g></svg>
        www.harborline.com
      </li>
    </ul>
  </section>
</body>
</html>
```